Veltrane Group Business Card Design

The CEO is looking for a new trendy look for his business card.
You can stay with current branding or come up with something new/creative. It can be 3D, including Medical Office buildings. You can use our logo in a variety of colors. Please include name, title, company name, company website, email address, cell number

Target Market(s)

Real Estate Development and Construction

Industry/Entity Type

Health care real estate

Contact Information for Business Card

Rohesh Kamdar, CEO M-604.781.2249 E-roheshkamdar@veltrane.com Address:4180 Lindqvist Ave, Tampa, FL 33482 www.veltrane.com

Font styles to use
Other font styles liked:
• Be creative

Requirements
Must have
• Creative, trendy look
Nice to have
• Please go to our website to get a feel- www. veltrane.com
Should not have
• small fonts

```html
<!DOCTYPE html>
<html lang="en">
<head>
<meta charset="utf-8">
<title>Veltrane Group – Business Card</title>
<link href="https://fonts.googleapis.com/css2?family=Montserrat:wght@400;700;800&display=swap" rel="stylesheet">
<style>
  :root {
    --brand-red: #b01e28;
    --brand-navy: #1c2f52;
    --card-black: #181818;
    --card-white: #ffffff;
    --text-light: #f2f2f2;
    --backdrop: #d9d8d4;
  }
  * { margin: 0; padding: 0; box-sizing: border-box; }
  html, body {
    width: 1200px; height: 801px; overflow: hidden;
    background: var(--backdrop);
    font-family: "Montserrat", sans-serif;
  }
  .canvas {
    position: relative; width: 1200px; height: 801px;
    display: flex; align-items: center; justify-content: center; gap: 40px;
  }
  .card {
    position: relative; width: 540px; height: 309px; overflow: hidden;
    border-bottom: 2px solid var(--brand-red);
    box-shadow: 0 14px 30px rgba(0,0,0,0.22);
  }
  /* Front */
  .card-front { background: var(--card-white); }
  .card-front .wave { position: absolute; inset: 0; width: 100%; height: 100%; }
  .front-wordmark {
    position: absolute; right: 30px; top: 28px;
    font-weight: 800; font-size: 40px; letter-spacing: -1px;
    color: var(--brand-red); line-height: 1;
  }
  .contact-block {
    position: absolute; left: 34px; top: 158px; color: var(--text-light);
  }
  .contact-block::before {
    content: ""; position: absolute; left: -34px; top: 2px;
    width: 14px; height: 36px; background: var(--brand-red);
  }
  .person-name {
    font-weight: 700; font-size: 18px; letter-spacing: 0.5px;
    color: var(--brand-red); text-transform: uppercase; line-height: 1.1;
  }
  .person-title { font-size: 12px; margin-top: 2px; }
  .address { font-size: 11px; line-height: 1.4; margin-top: 8px; }
  .contact-list { list-style: none; margin-top: 6px; font-size: 11px; line-height: 1.5; }
  .contact-list li { display: flex; align-items: center; gap: 7px; }
  .contact-list svg { width: 11px; height: 11px; flex: none; }
  /* Back */
  .card-back {
    background: var(--card-black);
    display: flex; align-items: center; justify-content: center;
  }
  .back-wordmark {
    font-weight: 800; font-size: 58px; letter-spacing: -1.5px;
    color: var(--brand-red); line-height: 1;
  }
</style>
</head>
<body>
<main class="canvas">

  <section class="card card-front">
    <svg class="wave" viewBox="0 0 540 309" preserveAspectRatio="none" aria-hidden="true">
      <path d="M0,44 C200,74 380,134 540,196 L540,309 L0,309 Z" fill="var(--brand-red)"/>
      <path d="M0,52 C200,82 380,142 540,204 L540,309 L0,309 Z" fill="var(--card-white)"/>
      <path d="M0,56 C200,86 380,146 540,208 L540,309 L0,309 Z" fill="var(--brand-navy)"/>
      <path d="M0,70 C200,100 380,160 540,222 L540,309 L0,309 Z" fill="var(--card-white)"/>
      <path d="M0,74 C200,104 380,164 540,226 L540,309 L0,309 Z" fill="var(--card-black)"/>
    </svg>

    <div class="front-wordmark">Veltrane Group</div>

    <div class="contact-block">
      <h1 class="person-name">Rohesh Kamdar</h1>
      <p class="person-title">CEO</p>
      <p class="address">4180 Lindqvist Ave,<br>Tampa, FL 33482</p>
      <ul class="contact-list">
        <li>
          <svg viewBox="0 0 12 12" aria-hidden="true"><rect x="3" y="0.5" width="6" height="11" rx="1.2" fill="none" stroke="var(--brand-red)" stroke-width="1.2"/><circle cx="6" cy="9.5" r="0.7" fill="var(--brand-red)"/></svg>
          604.781.2249
        </li>
        <li>
          <svg viewBox="0 0 12 12" aria-hidden="true"><rect x="0.5" y="2" width="11" height="8" fill="var(--brand-red)"/><path d="M0.5,2 L6,7 L11.5,2" fill="none" stroke="var(--card-black)" stroke-width="1"/></svg>
          roheshkamdar@veltrane.com
        </li>
        <li>
          <svg viewBox="0 0 12 12" aria-hidden="true"><circle cx="6" cy="6" r="5.5" fill="var(--brand-red)"/><path d="M0.5,6 H11.5 M6,0.5 C3,3 3,9 6,11.5 M6,0.5 C9,3 9,9 6,11.5" fill="none" stroke="var(--card-black)" stroke-width="0.8"/></svg>
          www.veltrane.com
        </li>
      </ul>
    </div>
  </section>

  <section class="card card-back">
    <div class="back-wordmark">Veltrane Group</div>
  </section>

</main>
</body>
</html>
```